BUSINESS CARD - HALLORAN FIELD SERVICES

I would like to create a business card for my fertilizer spreading business. I would like to incorporate my existing logo and also a description of the services offered. The business card will be given to farmers so must be kept simple but effective. It will also be left in stores so much also be eye catching in order to stand out from other cards.

Target Market(s)

FARMERS

Requirements
Must have
• FRONT OF CARD = EXISTING LOGO + "CUSTOMISED SPREADING" below the logo

REAR Of CARD = SERVICES OFFERED AND CONTACT DETAILS

- Bulk fertilizer including Lime, Gypsum, Manure & Compost
- Granular fertilizer including Single Super, Urea, Gran-am, & Custom Blends
- Modern equipment - Autosteer & Variable Rate Capable
- Friendly & Reliable Service
- Contact Gus: 0417 552 308
Nice to have
• utilize same color scheme as existing logo

```html
<!DOCTYPE html>
<html lang="en">
<head>
<meta charset="UTF-8">
<title>Halloran Field Services – Business Card</title>
<link rel="stylesheet" href="https://fonts.googleapis.com/css2?family=Montserrat:wght@400;500;600;700&display=swap">
<style>
  :root {
    --bg: #ece9e4;
    --card-white: #ffffff;
    --ink: #4a4a4c;
    --ink-soft: #5b5b5e;
    --accent: #f39a2a;
    --rear-top: #6a6a6d;
    --rear-bottom: #545456;
    --art-light: #8d8d90;
    --art-dark: #5c5c5f;
    --on-dark: #ffffff;
  }
  * { box-sizing: border-box; margin: 0; padding: 0; }
  html, body { width: 1200px; height: 1200px; overflow: hidden; }
  body {
    background: var(--bg);
    font-family: "Montserrat", sans-serif;
    position: relative;
  }
  .card {
    position: absolute;
    left: 262px;
    width: 685px;
    height: 392px;
    border-radius: 22px;
    overflow: hidden;
    box-shadow: 0 8px 22px rgba(0,0,0,0.18);
  }
  /* Front */
  .card--front { top: 165px; background: var(--card-white); }
  .front-art {
    position: absolute;
    left: 0; top: 36px;
    width: 412px; height: 356px;
    border-radius: 0 200px 0 0;
    background: linear-gradient(160deg, var(--art-light), var(--art-dark));
    opacity: 0.85;
  }
  .front-details {
    position: absolute;
    right: 38px; top: 243px;
    text-align: right;
    color: var(--ink-soft);
  }
  .person-name {
    font-size: 22px; font-weight: 600; letter-spacing: 0.3px;
    color: var(--ink);
  }
  .person-role {
    font-size: 15px; font-weight: 400; color: var(--accent);
    margin-top: 3px;
  }
  .contact-list { list-style: none; margin-top: 14px; }
  .contact-list li {
    font-size: 15px; line-height: 19.5px;
    display: flex; justify-content: flex-end; align-items: center; gap: 8px;
  }
  .contact-list svg { width: 13px; height: 13px; fill: var(--ink); flex: none; }
  /* Rear */
  .card--rear {
    top: 653px;
    background: linear-gradient(180deg, var(--rear-top), var(--rear-bottom));
    color: var(--on-dark);
    text-align: center;
  }
  .brand-mark {
    position: absolute;
    left: 50%; top: 88px;
    width: 94px; height: 94px;
    margin-left: -47px;
    border-radius: 50%;
    background: var(--art-light);
  }
  .brand-name {
    position: absolute; left: 0; right: 0; top: 192px;
    font-size: 26px; font-weight: 700; letter-spacing: -0.3px;
  }
  .brand-tagline {
    position: absolute; left: 0; right: 0; top: 244px;
    font-size: 16px; font-weight: 400; letter-spacing: 2.4px;
  }
  .service-list {
    position: absolute; left: 0; right: 0; top: 289px;
    list-style: none;
    font-size: 15px; line-height: 19.5px; font-weight: 400;
  }
</style>
</head>
<body>
  <section class="card card--front">
    <div class="front-art" role="img" aria-label="Farm illustration of a cow and sheep on grass under a wheat stalk arc with an orange sprout"></div>
    <div class="front-details">
      <p class="person-name">DANIEL REEVE</p>
      <p class="person-role">President</p>
      <ul class="contact-list">
        <li>0417 552 308
          <svg viewBox="0 0 24 24" aria-hidden="true"><path d="M6.6 10.8a15.1 15.1 0 0 0 6.6 6.6l2.2-2.2a1 1 0 0 1 1-.25 11.4 11.4 0 0 0 3.6.57 1 1 0 0 1 1 1V20a1 1 0 0 1-1 1A17 17 0 0 1 3 4a1 1 0 0 1 1-1h3.5a1 1 0 0 1 1 1c0 1.25.2 2.45.57 3.57a1 1 0 0 1-.25 1z"/></svg>
        </li>
        <li>info@halloranfield.com
          <svg viewBox="0 0 24 24" aria-hidden="true"><path d="M2 5h20v14H2z M3.5 6.5v.6L12 12.5l8.5-5.4v-.6z" fill-rule="evenodd"/></svg>
        </li>
        <li>www.halloranfield.com
          <svg viewBox="0 0 24 24" aria-hidden="true"><circle cx="12" cy="12" r="10"/></svg>
        </li>
      </ul>
    </div>
  </section>

  <section class="card card--rear">
    <div class="brand-mark" aria-hidden="true"></div>
    <p class="brand-name">Halloran Field Services</p>
    <p class="brand-tagline">CUSTOMISED SPREADING</p>
    <ul class="service-list">
      <li>Bulk fertilizer including Lime, Gypsum, Manure &amp; Compost</li>
      <li>Granular fertilizer including Single Super, Urea, Gran-am, &amp; Custom Blends</li>
      <li>Modern equipment - Autosteer &amp; Variable Rate Capable</li>
      <li>Friendly &amp; Reliable Service</li>
    </ul>
  </section>
</body>
</html>
```